Modern and Sleek Non-Fiction Book Cover Design

Seeking a talented graphic designer to create a modern and sleek cover and back page for a book to be published on Folionet . The design should be visually appealing and align with the book's theme, using bright colors to make it stand out. The title is "A Studio Ledger Field Manual" with "The" in a smaller font, and the tagline "Intake as a Competitive Advantage" should be included. The book is targeted at an audience interested in immigration and family law firms. So I would like it on the cover as well. The hex numbers for the colors are 00aeeef, fcb034, and 336a89. The cover should feature the author's photo prominently.
Deliverables
-Design a modern front cover for the book
-Design a sleek back page for the book
-Ensure designs meet Folionet publishing requirements 8x5 paperback
Let's not use the side image, it doesn't seem to fit like I thought it might.

```html
<!DOCTYPE html>
<html lang="en">
<head>
<meta charset="utf-8">
<title>A Studio Ledger Field Manual — Cover Spread</title>
<link rel="stylesheet" href="https://fonts.googleapis.com/css2?family=Outfit:wght@300;400;700;800&family=Questrial&display=swap">
<style>
  :root{
    --stage:#4e4e4e;
    --back:#3d3d3d;
    --spine:#474747;
    --front-top:#656564;
    --front-bottom:#555554;
    --gold:#e3b340;
    --amber:#d88a2b;
    --white:#ffffff;
    --body:#e9e9e9;
    --tag:#262626;
    --band:rgba(60,60,60,.85);
  }
  *{margin:0;padding:0;box-sizing:border-box}
  html,body{width:1200px;height:960px;overflow:hidden;background:var(--stage)}
  .spread{position:absolute;left:50px;top:92px;width:1100px;height:776px;display:flex}

  /* back cover */
  .back-cover{position:relative;width:506px;height:100%;background:var(--back)}
  .back-title{position:absolute;left:116px;top:66px;font:700 22px/24px "Outfit",sans-serif;letter-spacing:.04em;color:var(--amber)}
  .back-title .accent{color:var(--white)}
  .back-copy{position:absolute;font:400 11.4px/15.8px "Questrial",sans-serif;color:var(--body);text-align:justify;letter-spacing:.06em}
  .back-copy p+p{margin-top:5px}
  .copy-intro{left:116px;top:124px;width:272px}
  .copy-bio{left:150px;top:340px;width:236px}
  .author-tag{position:absolute;left:114px;top:346px;width:28px;height:182px;background:var(--tag);border-top:4px solid var(--amber);display:flex;align-items:flex-end;justify-content:center;padding-bottom:20px}
  .author-tag span{writing-mode:vertical-rl;transform:rotate(180deg);font:300 15px/1 "Outfit",sans-serif;letter-spacing:.02em;color:var(--body);white-space:nowrap}
  .imprint{position:absolute;left:208px;top:712px;display:flex;align-items:center;gap:6px;font:700 17px/1 "Outfit",sans-serif;color:var(--white)}
  .imprint i{width:9px;height:9px;background:var(--white);display:block}

  /* spine */
  .spine{position:relative;width:82px;height:100%;background:var(--spine);border-right:2px solid #8a8a8a}
  .spine-text{position:absolute;left:26px;top:64px;writing-mode:vertical-rl;white-space:nowrap}
  .spine-title{font:700 23px/1 "Outfit",sans-serif;letter-spacing:.03em;color:var(--gold)}
  .spine-title .accent{color:var(--white)}
  .spine-author{display:inline-block;margin-top:70px;font:300 23px/1 "Outfit",sans-serif;color:var(--white)}

  /* front cover */
  .front-cover{position:relative;flex:1;height:100%;background:linear-gradient(180deg,var(--front-top),var(--front-bottom));overflow:hidden}
  .author-photo{position:absolute;left:176px;top:300px;width:336px;height:476px;background:radial-gradient(ellipse 44% 30% at 62% 34%,#c79a86 0%,#a5806f 55%,transparent 75%),linear-gradient(180deg,transparent 0%,transparent 52%,#151515 70%,#0e0e0e 100%)}
  .front-title{position:absolute;left:32px;top:72px;font:800 64px/61px "Outfit",sans-serif;letter-spacing:-.04em;color:var(--gold)}
  .front-title .accent{color:var(--white)}
  .title-rule{position:absolute;left:262px;width:1px;background:var(--white)}
  .rule-upper{top:84px;height:180px}
  .rule-lower{top:328px;height:116px}
  .tagline{position:absolute;left:32px;top:484px;font:300 24px/33px "Outfit",sans-serif;color:var(--gold);letter-spacing:-.01em}
  .tagline svg{display:inline-block;width:20px;height:22px;vertical-align:-2px;margin:0 -1px}
  .author-band{position:absolute;left:300px;top:734px;right:0;height:42px;background:var(--band);display:flex;align-items:center;justify-content:center;font:300 21px/1 "Outfit",sans-serif;color:var(--white)}
</style>
</head>
<body>
<main class="spread">
  <section class="back-cover">
    <h2 class="back-title">A Studio Ledger Field<br><span class="accent">Manual</span></h2>
    <div class="back-copy copy-intro">
      <p>What makes us unique in the legal field is we spent two years embedded in a large local immigration law firm with the ability to experiment and test campaigns, ads, and copy to get uncommon results. Soon law firms from Texas to California were requesting the same type of results we achieved right here in Dallas. A year later, we’ve launched our own podcast introducing legal consumers to some of the top U.S. immigration attorneys. It’s our way of giving back and using the relationships we’ve made to provide answers to people’s most common questions about legal immigration.</p>
    </div>
    <div class="author-tag"><span>DALE WHITMORE</span></div>
    <div class="back-copy copy-bio">
      <p>I have more than a decade of experience as a Senior Executive/Officer in billion-dollar Print Marketing and Direct Mail companies (including as Chief Marketing Officer).</p>
      <p>Since 2011, I’ve been the Founder and President of Northvale, LLC a Full-Service International award-winning Digital Marketing Agency serving clients primarily in the home services and legal fields.</p>
      <p>My perspective comes from working with both best-in-class Fortune 500 clients and entrepreneurs of niche small businesses. I am a former marketing mentor to startups associated with Forge Lab incubator and the Harlow Economic Development corporation.</p>
    </div>
    <div class="imprint"><i></i>Northvale</div>
  </section>

  <section class="spine">
    <div class="spine-text">
      <span class="spine-title">A Studio Ledger Field <span class="accent">Manual</span></span>
      <span class="spine-author">DALE WHITMORE</span>
    </div>
  </section>

  <section class="front-cover">
    <div class="author-photo" role="img" aria-label="Portrait photograph of the author, Dale Whitmore, in a black shirt"></div>
    <h1 class="front-title">A<br>Studio<br>Ledger<br>Field<br><span class="accent">Man<br>ual</span></h1>
    <span class="title-rule rule-upper"></span>
    <span class="title-rule rule-lower"></span>
    <p class="tagline">INTAKE AS A<br>COMPETITIVE<br>AD<svg viewBox="0 0 20 22" aria-hidden="true"><path d="M1 12 L8 20 L19 1" fill="none" stroke="#ffffff" stroke-width="2.2"/></svg>ANTAGE</p>
    <div class="author-band">DALE WHITMORE</div>
  </section>
</main>
</body>
</html>
```